Request for Business Card Design

Hi. My name is Marlene, I am looking for a new business card design for my company, Quarrow Signal Instruments, LLC. I really like the design you did for Tarsel Venture and was hoping you could do something similar using our full logo and our mark. I am also open to any raised texture design using our mark. I have attached our full logo, which would need to be somewhere on the card, as well as the mark in both outline and full form, as well as our brand colors / guide. The card does not have to be white, as long as our logo and mark appear. I actually like darker colored business cards more, but am open to all options. If you are interested in working with me, please let me know. We would also take the business card design into letterhead design if you can do that.

```html
<!DOCTYPE html>
<html lang="en">
<head>
<meta charset="utf-8">
<title>Quarrow Signal Instruments — Business Card</title>
<link rel="stylesheet" href="https://fonts.googleapis.com/css2?family=Open+Sans:wght@400;600;700&display=swap">
<style>
  :root {
    --backdrop: #e9e6e1;
    --card: #1f2024;
    --card-deep: #141518;
    --brand-blue: #1b9ec9;
    --ink-light: #f2f2f2;
    --ink-muted: #5a5c61;
    --emboss: #18191c;
  }
  * { box-sizing: border-box; margin: 0; padding: 0; }
  html, body {
    width: 1200px; height: 780px; overflow: hidden;
    background: var(--backdrop);
    font-family: "Open Sans", sans-serif;
  }
  .stage {
    width: 1200px; height: 780px;
    display: flex; align-items: center; justify-content: center; gap: 40px;
  }
  .card {
    position: relative;
    width: 540px; height: 310px;
    background: var(--card);
    border-radius: 4px;
    overflow: hidden;
    box-shadow: 0 10px 28px rgba(0,0,0,0.25);
  }

  /* Front */
  .brand {
    position: absolute; top: 22px; left: 24px;
    display: flex; align-items: center; gap: 10px;
  }
  .brand-dot {
    width: 30px; height: 30px; border-radius: 50%;
    background: var(--brand-blue);
  }
  .brand-name {
    color: var(--ink-muted);
    font-weight: 700; font-size: 24px; letter-spacing: 3px; line-height: 1;
  }
  .brand-tagline {
    color: var(--ink-muted);
    font-weight: 700; font-size: 8px; letter-spacing: 1.2px; margin-top: 3px;
  }
  .contact {
    position: absolute; top: 100px; left: 24px;
    color: var(--ink-light); font-size: 12.5px; line-height: 1.55;
  }
  .contact-address { margin-bottom: 4px; }
  .contact-line { display: flex; align-items: center; gap: 8px; }
  .contact-line svg { width: 11px; height: 11px; flex: none; }
  .feature-disc {
    position: absolute; left: 230px; top: 150px;
    width: 230px; height: 230px; border-radius: 50%;
    background: radial-gradient(circle at 65% 35%, #2d2f34, var(--card-deep) 70%);
  }
  .holder {
    position: absolute; right: 40px; top: 196px; text-align: right;
  }
  .holder-name {
    color: var(--brand-blue); font-weight: 700; font-size: 34px; line-height: 1;
  }
  .holder-role {
    color: var(--ink-light); font-size: 15px; margin-top: 4px;
  }
  .accent-bar {
    position: absolute; right: 0; top: 250px;
    width: 26px; height: 34px; background: var(--brand-blue);
  }

  /* Back */
  .back-brand {
    position: absolute; inset: 0;
    display: flex; align-items: center; justify-content: center; gap: 16px;
  }
  .back-dot {
    width: 52px; height: 52px; border-radius: 50%; background: var(--emboss);
  }
  .back-name {
    color: var(--emboss); font-weight: 700; font-size: 40px; letter-spacing: 5px; line-height: 1;
  }
  .back-tagline {
    color: var(--emboss); font-weight: 700; font-size: 12px; letter-spacing: 1.8px; margin-top: 4px;
  }
</style>
</head>
<body>
<main class="stage">
  <section class="card card-front" aria-label="Business card front">
    <div class="brand">
      <span class="brand-dot"></span>
      <div>
        <div class="brand-name">QUARROW</div>
        <div class="brand-tagline">SIGNAL INSTRUMENTS</div>
      </div>
    </div>

    <div class="feature-disc"></div>

    <div class="contact">
      <p class="contact-address">1180 Harrow Field Road ·<br>Brenton, CO 80217</p>
      <p class="contact-line">
        <svg viewBox="0 0 12 12"><path d="M3 1 L5 3.5 L4 5 Q5 7 7 8 L8.5 7 L11 9 L9.5 11 Q5 11 2 7 Q0.5 4 1 2.5 Z" fill="var(--brand-blue)"/></svg>
        +001 303 555 0142
      </p>
      <p class="contact-line">
        <svg viewBox="0 0 12 12"><rect x="1" y="4" width="10" height="7" rx="1" fill="var(--brand-blue)"/><rect x="3" y="1" width="6" height="4" fill="none" stroke="var(--brand-blue)"/></svg>
        +001 303 555 0178
      </p>
      <p class="contact-line">
        <svg viewBox="0 0 12 12"><circle cx="6" cy="6" r="5" fill="none" stroke="var(--brand-blue)" stroke-width="1.4"/><path d="M1 6 H11 M6 1 Q9 6 6 11 Q3 6 6 1" fill="none" stroke="var(--brand-blue)"/></svg>
        www.quarrowsignal.com
      </p>
      <p class="contact-line">
        <svg viewBox="0 0 12 12"><rect x="1" y="2.5" width="10" height="7" rx="1" fill="var(--brand-blue)"/><path d="M1.5 3 L6 6.5 L10.5 3" fill="none" stroke="var(--card)"/></svg>
        info@quarrowsignal.com
      </p>
    </div>

    <div class="holder">
      <p class="holder-name">Marlene</p>
      <p class="holder-role">Director</p>
    </div>
    <span class="accent-bar"></span>
  </section>

  <section class="card card-back" aria-label="Business card back">
    <div class="back-brand">
      <span class="back-dot"></span>
      <div>
        <div class="back-name">QUARROW</div>
        <div class="back-tagline">SIGNAL INSTRUMENTS</div>
      </div>
    </div>
  </section>
</main>
</body>
</html>
```